U.S. Popcorn company needs business cards

We are a popcorn company that manufactures popcorn and sells it to grocery stores worldwide. Our theme is "Americana" and our logo is U.S. route 66 which is the most famous highway in the U.S.

We would like the design to be simple and to use both sides. On the back side we would like to see just the logo and website. The front would be normal details

Target Market(s)

Wholesalers, grocers and distributors

Industry/Entity Type

Manufacture

Contact Information for Business Card

Business name: Prairie Lantern Popcorn
Phone: +1 555 308 4726
Email: Dale@prairielanternpopcorn.com
website: www.prairielanternpopcorn.com
Tag Line: "POPped with pride"
Name: Dale Whitcombe
Title: Founder/President

Requirements
Must have
• Either this design should be fun or clean and simple. I will let you show me your thougths.
Nice to have
• Anything that ties in the real Hwy Route 66.
• Colors might need to be red, white and blue incorporated.
Should not have
• Not be too busy.

```html
<!DOCTYPE html>
<html lang="en">
<head>
<meta charset="utf-8">
<title>Prairie Lantern Popcorn – Business Cards</title>
<link rel="stylesheet" href="https://fonts.googleapis.com/css2?family=Mulish:ital,wght@0,400;0,600;0,700;0,800;1,400&display=swap">
<style>
  :root {
    --navy: #0f2e66;
    --red: #c8151b;
    --white: #ffffff;
    --paper: #f4f4f4;
    --backdrop: #e6e6e6;
    --ink: #1e2f5c;
    --muted: #444a59;
  }
  * { box-sizing: border-box; margin: 0; padding: 0; }
  html, body {
    width: 1200px; height: 576px; overflow: hidden;
    background: var(--backdrop);
    font-family: "Mulish", sans-serif;
  }
  .canvas { position: relative; width: 1200px; height: 576px; }

  .card {
    position: absolute;
    width: 484px; height: 292px;
    border-radius: 6px;
    overflow: hidden;
  }

  /* Back side */
  .card-back {
    left: 82px; top: 139px;
    background: var(--navy);
  }
  .card-back .brand-name {
    position: absolute; left: 0; right: 0; top: 104px;
    text-align: center;
    color: var(--white);
    font-weight: 800;
    font-size: 30px;
    line-height: 1.15;
    letter-spacing: 0.5px;
  }
  .card-back .website {
    position: absolute; left: 0; right: 0; top: 256px;
    display: flex; align-items: center; justify-content: center; gap: 12px;
    color: var(--white);
    font-weight: 600;
    font-size: 11.5px;
    letter-spacing: 0.3px;
  }
  .card-back .website .rule {
    width: 44px; height: 2px; background: var(--red);
  }

  /* Front side */
  .card-front {
    left: 602px; top: 138px;
    width: 481px; height: 291px;
    background: var(--paper);
  }
  .side-band {
    position: absolute; left: 0; top: 0; bottom: 0;
    width: 41px; background: var(--navy);
    border-right: 4px solid var(--red);
  }
  .tagline {
    position: absolute; left: 20px; top: 150px;
    transform: translate(-50%, -50%) rotate(-90deg);
    white-space: nowrap;
    color: var(--white);
    font-size: 13px;
    letter-spacing: 0.3px;
  }
  .tagline strong { font-weight: 800; }
  .card-front .brand-name {
    position: absolute; right: 36px; top: 62px;
    width: 150px;
    text-align: center;
    color: var(--navy);
    font-weight: 800;
    font-size: 19px;
    line-height: 1.15;
  }
  .person {
    position: absolute; left: 68px; top: 170px;
  }
  .person-name {
    color: var(--red);
    font-weight: 700;
    font-size: 16px;
  }
  .person-title {
    color: var(--muted);
    font-style: italic;
    font-size: 12px;
    margin-top: 2px;
  }
  .contacts {
    position: absolute; left: 72px; top: 218px;
    list-style: none;
  }
  .contacts li {
    display: flex; align-items: center; gap: 10px;
    height: 18px;
    color: var(--ink);
    font-size: 13px;
  }
  .contacts svg { width: 11px; height: 11px; flex: none; }
</style>
</head>
<body>
<main class="canvas">

  <section class="card card-back" aria-label="Card back">
    <p class="brand-name">Prairie Lantern<br>Popcorn</p>
    <p class="website"><span class="rule"></span>www.prairielanternpopcorn.com<span class="rule"></span></p>
  </section>

  <section class="card card-front" aria-label="Card front">
    <div class="side-band"></div>
    <p class="tagline">"<strong>POP</strong>ped with pride"</p>

    <p class="brand-name">Prairie Lantern Popcorn</p>

    <div class="person">
      <p class="person-name">Dale Whitcombe</p>
      <p class="person-title">Founder/President</p>
    </div>

    <ul class="contacts">
      <li>
        <svg viewBox="0 0 12 12" aria-hidden="true"><path fill="#c8151b" d="M1 4c0-2 2-3 5-3s5 1 5 3l-2 1-1-1.5H4L3 5 1 4zm2 2h6l1 5H2l1-5zm3 1a1.5 1.5 0 100 3 1.5 1.5 0 000-3z"/></svg>
        +1 555 308 4726
      </li>
      <li>
        <svg viewBox="0 0 12 12" aria-hidden="true"><rect x="0.5" y="2" width="11" height="8" fill="#c8151b"/><path d="M0.5 2l5.5 4.5L11.5 2" fill="none" stroke="#fff" stroke-width="1"/></svg>
        Dale@prairielanternpopcorn.com
      </li>
      <li>
        <svg viewBox="0 0 12 12" aria-hidden="true"><circle cx="6" cy="6" r="5" fill="#c8151b"/><path d="M1 6h10M6 1c-2.5 3-2.5 7 0 10M6 1c2.5 3 2.5 7 0 10" fill="none" stroke="#fff" stroke-width="0.8"/></svg>
        www.prairielanternpopcorn.com
      </li>
    </ul>
  </section>

</main>
</body>
</html>
```